Web Design Project

We need a web design company for a company based in London. We are an online minicab booking service that produces real time quotes on cab journey for consumers. Our colours are currently red and yellow, but do not need to stay that way; it's open to interpretation. Please avoid yellow and black as a colour combination. Our current site is: www.rovelink.co.uk We are looking for a new site to be user-friendly and easy to use, but more polished and professional looking, without using it usability and simplicity. We need to keep the booking capability on each page and it needs to draw in the user's eye. We need a site that is reliable and easy to use, but also fun.

Main objective: keep it simple, like it is now, but polish it up some. Also, we need to be able to add more content to it. And, we will also be adding a login capability for return users.

Target Market(s)

Internet-savvy people aged 18 and older.

Industry/Entity Type

It Company

Requirements
Must have
• Must have the booking widget. However, it doesn't have to be as large as it is now. We are actually thinking to split it over two pages. We will add a few options to the booking widget, such as another via option. The booking widget must be the most noticeable feature on the page. Sans serif font, please.
Should not have
• Should not be too busy and distracting. Please do not use any images of traditional taxis, ie. black cabs from London or yellow cabs from NYC. Our cars do not resemble these and our business cannot be associated with these images.

```html
<!DOCTYPE html>
<html lang="en">
<head>
<meta charset="utf-8">
<title>Rovelink.co.uk – Book a Cab</title>
<link rel="stylesheet" href="https://fonts.googleapis.com/css2?family=Arimo:ital,wght@0,400;0,700;1,400&family=PT+Sans:wght@400;700&display=swap">
<style>
:root{
  --bg-dark:#2b2b2b;
  --bg-mid:#3a3a3a;
  --page:#ffffff;
  --brand-red:#b3200f;
  --brand-red-dark:#8c1608;
  --brand-yellow:#f2c42c;
  --panel-yellow:#f3ca35;
  --gold-text:#d4a11a;
  --ink:#222222;
  --body:#555555;
  --rule:#cccccc;
  --btn-dark:#2e2e2e;
  --photo-a:#3a3428;
  --photo-b:#8a6a34;
}
*{box-sizing:border-box;margin:0;padding:0}
html,body{width:1123px;height:1200px;overflow:hidden}
body{
  background:linear-gradient(180deg,var(--bg-mid) 0%,var(--bg-dark) 100%);
  font-family:"Arimo",Arial,sans-serif;color:var(--ink);position:relative;
}
.page{position:absolute;z-index:1;left:136px;top:43px;width:848px;height:1081px;background:var(--page);border-top:5px solid var(--brand-yellow)}
.abs{position:absolute}
.logo{left:75px;top:23px;display:flex;align-items:center;gap:18px}
.logo-dot{width:42px;height:42px;border-radius:50%;background:var(--brand-yellow)}
.logo-name{font-family:"PT Sans",sans-serif;font-size:32px;color:var(--ink)}
.booking-line{left:483px;top:30px;display:flex;align-items:center;gap:14px;font-size:18px;color:var(--brand-red)}
.booking-line b{color:var(--ink);font-weight:700}
.nav{position:absolute;z-index:5;left:127px;top:131px;width:867px;height:65px;background:linear-gradient(180deg,#c42812,var(--brand-red-dark));box-shadow:0 3px 6px rgba(0,0,0,.35)}
.nav a{position:absolute;top:20px;color:#fff;font-family:"PT Sans",sans-serif;font-size:20px;text-decoration:none;white-space:nowrap}
.nav .home{left:62px;top:16px;width:78px;height:33px;border:2px solid #7a1204;background:#9d1a0a;text-align:center;line-height:29px;color:#f2c0a0;top:14px}
.nav .small{font-family:"Arimo",sans-serif;font-size:10px;top:27px;color:#3b0c04;text-decoration:underline}
.hero-photo{left:53px;top:168px;width:469px;height:352px;background:radial-gradient(ellipse at 40% 30%,var(--photo-b),var(--photo-a) 70%)}
.booker{left:523px;top:168px;width:271px;height:352px;background:linear-gradient(180deg,var(--panel-yellow),#f0c02a);padding:0 18px}
.booker h2{font-family:"PT Sans",sans-serif;font-weight:700;font-size:27px;color:#2a2a2a;margin-top:18px;padding-bottom:4px;border-bottom:1px solid #fff3c0}
.booker label{display:block;font-size:12px;color:#333;margin-top:11px;margin-bottom:7px}
.field{display:flex;height:27px}
.field .input{flex:0 0 180px;background:#fff;font-size:10px;font-style:italic;color:#999;padding:8px 0 0 12px}
.field .find{flex:0 0 54px;background:var(--btn-dark);color:#fff;font-size:12px;font-weight:700;text-align:center;line-height:27px}
.date{display:flex;align-items:center;gap:16px;height:30px}
.date .input{font-style:normal;color:#777;height:25px;padding-top:7px}
.see-all{display:block;text-align:right;font-size:10px;color:#333;text-decoration:underline;margin-top:18px}
.quote-btn{display:block;margin-top:34px;height:30px;background:linear-gradient(180deg,#4a4a4a,#222);border-radius:3px;color:#fff;font-family:"PT Sans",sans-serif;font-weight:700;font-size:15px;text-align:center;line-height:30px}
.steps{left:53px;top:551px;width:380px}
.steps h3{font-weight:400;font-size:21px;color:#111}
.steps .lead{font-size:14px;margin-top:10px}
.steps ol{list-style:none;margin-top:24px}
.steps li{display:flex;align-items:center;gap:22px;height:45px;font-size:13.5px;font-weight:700;color:#333}
.steps li span{width:26px;height:26px;border-radius:50%;background:var(--brand-red);color:#fff;font-size:14px;text-align:center;line-height:26px}
.divider{left:433px;top:557px;width:1px;height:240px;background:var(--rule)}
.why{left:460px;top:553px;width:340px}
.why h3{font-weight:400;font-size:20px;color:var(--brand-red)}
.why h4{font-size:13.5px;margin-top:14px;color:#333}
.why p{font-size:11.5px;line-height:21px;color:var(--body);margin-top:6px}
.stories{left:53px;top:822px;width:743px}
.stories h3{font-weight:400;font-size:17px;color:var(--gold-text);padding-bottom:6px;border-bottom:1px solid #bbb;width:738px}
.stories p{font-size:12.3px;line-height:21.3px;color:var(--body);margin-top:8px;text-align:justify}
.ask{left:54px;top:1014px;font-size:13px;font-style:italic;color:#222}
.ask a{color:#1a3a9a;font-size:16px}
.read-more{left:704px;top:999px;width:90px;height:28px;background:var(--btn-dark);color:#fff;border-radius:3px;font-size:13px;text-align:center;line-height:28px}
.footer{left:190px;top:1144px;font-size:10px;color:#eee}
.footer a{color:var(--brand-yellow)}
.footer .plain{color:#eee}
.social{left:830px;top:1138px;display:flex;gap:9px}
.social span{width:26px;height:26px;border-radius:50%;background:#cfcfcf}
</style>
</head>
<body>
<main class="page">
  <div class="abs logo"><span class="logo-dot"></span><span class="logo-name">Rovelink.co.uk</span></div>
  <div class="abs booking-line">
    <svg width="34" height="34" viewBox="0 0 34 34" aria-hidden="true"><circle cx="17" cy="17" r="17" fill="#b3200f"/><path d="M12 9c1-1 2 0 3 2l1 2c0 1-1 2-2 2 1 2 3 4 5 5 0-1 1-2 2-2l2 1c2 1 3 2 2 3l-2 2c-5 0-12-7-12-12z" fill="#fff"/></svg>
    <span>Booking Line: <b>020 7946 0321</b></span>
  </div>

  <div class="abs hero-photo" role="img" aria-label="Photo of cabs waiting in a lit underground rank"></div>
  <form class="abs booker">
    <h2>BOOK A CAB</h2>
    <label>Pick me up from:</label>
    <div class="field"><span class="input">e.g. pick up address or post code</span><span class="find">Find</span></div>
    <label>Drop me at:</label>
    <div class="field"><span class="input">e.g. drop address or post code</span><span class="find">Find</span></div>
    <label>Pick up date and time:</label>
    <div class="date field"><span class="input">5 Apr 2012 @ 12:02</span>
      <svg width="37" height="30" viewBox="0 0 37 30" aria-hidden="true"><rect x="1" y="1" width="35" height="28" fill="#fff" stroke="#2a6fb0"/><rect x="1" y="1" width="35" height="7" fill="#2a6fb0"/><g fill="#9bbfe0"><rect x="5" y="12" width="5" height="4"/><rect x="13" y="12" width="5" height="4"/><rect x="21" y="12" width="5" height="4"/><rect x="29" y="12" width="4" height="4"/><rect x="5" y="20" width="5" height="4"/><rect x="13" y="20" width="5" height="4"/><rect x="21" y="20" width="5" height="4"/></g></svg>
    </div>
    <a class="see-all">See all options</a>
    <span class="quote-btn">Get your no obligation quotes</span>
  </form>

  <section class="abs steps">
    <h3>As easy as opening the cab's door</h3>
    <p class="lead">Its free, dependable and with no obligation</p>
    <ol>
      <li><span>1</span>Enter your route</li>
      <li><span>2</span>Quickly compare taxi fares</li>
      <li><span>3</span>Get your travel confirmed on your phone by SMS.</li>
    </ol>
  </section>
  <div class="abs divider"></div>
  <section class="abs why">
    <h3>WHY ROVELINK?</h3>
    <h4>Price</h4>
    <p>Rovelink guarantees that you get the best deal for your travel, as you get quotes from several cab companies.</p>
    <h4>No fees</h4>
    <p>There's absolutely no cost for you to use our service.</p>
    <h4>Coverage</h4>
    <p>Rovelink has the largest database of licensed minicab operators. You can use Rovelink wherever you are in greater London.</p>
  </section>

  <section class="abs stories">
    <h3>THE BEST STORIES FROM OUR COMMUNITY</h3>
    <p>I recently hit London for a girlie night on the town with my bestie. After a little too much champagne, we had a stupid argument and decided to leave the club early. In the cab on our way home, we didn't say one word to each other. The driver who could sense we were both upset however, had other plans. He randomly started singing Lumen's Summer Nights! My best friend and I were in shock, we looked at each other and couldn't stop laughing! The remainder of the journey consisted of us all belting out Lumen classics, in between fits of laughter. We were so disappointed when we arrived home as we wanted to continue the fun, we will never forget our singing taxi driver!</p>
  </section>
  <p class="abs ask">Do you have your story? <a>Send</a> us it!</p>
  <span class="abs read-more">Read more</span>
</main>
<nav class="nav">
  <a class="home">Home</a>
  <a style="left:177px">Rovelink Miles</a>
  <a style="left:348px">Join Us</a>
  <a style="left:461px">About Us</a>
  <a style="left:589px">Contact</a>
  <a class="small" style="left:723px">Log In</a>
  <a class="small" style="left:767px">Sign Up</a>
</nav>
<footer>
  <p class="abs footer">© <a>Rovelink</a> 2011-2012 | <span class="plain" style="text-decoration:underline">Privacy Policy</span></p>
  <div class="abs social" aria-label="Social links"><span></span><span></span><span></span></div>
</footer>
</body>
</html>
```